Business Cards for a law firm

Business cards for our law firm. Use our silhoette logo and OAK PARTNERS - check our website (www.oakpartners.example)

Contact Information for Business Card

our silhouette logo, OAK PARTNERS, 800-555-0147, Dorian Pemberton, dorian@oakpartners.example

Requirements
Must have
• our silhouette logo, OAK PARTNERS, 800-555-0147, Dorian Pemberton, dorian@oakpartners.example

```html
<!DOCTYPE html>
<html lang="en">
<head>
<meta charset="utf-8">
<title>Oak Partners – Business Cards</title>
<link rel="stylesheet" href="https://fonts.googleapis.com/css2?family=Roboto:wght@400;500;700&display=swap">
<style>
  :root {
    --backdrop: #e3e8ea;
    --navy: #23346a;
    --navy-deep: #22336a;
    --emboss-blue: #3a78c4;
    --card-white: #ffffff;
    --ink: #24356b;
  }
  * { box-sizing: border-box; margin: 0; padding: 0; }
  html, body { width: 1200px; height: 960px; overflow: hidden; }
  body {
    background: var(--backdrop);
    font-family: "Roboto", Arial, sans-serif;
    position: relative;
  }
  .card {
    position: absolute;
    border-radius: 26px;
    overflow: hidden;
  }
  .card--front {
    left: 246px; top: 58px; width: 709px; height: 406px;
    background: var(--navy-deep);
  }
  .card--back {
    left: 250px; top: 501px; width: 702px; height: 401px;
    background: var(--card-white);
  }
  .brand {
    position: absolute;
    display: flex;
    align-items: center;
  }
  .brand__mark {
    border-radius: 50%;
    flex: none;
  }
  .brand__name {
    font-family: "Roboto", Arial, sans-serif;
    font-weight: 400;
    line-height: 0.95;
    text-transform: uppercase;
  }
  .card--front .brand { left: 116px; top: 130px; }
  .card--front .brand__mark {
    width: 96px; height: 96px;
    background: var(--emboss-blue);
    margin-right: 26px;
  }
  .card--front .brand__name {
    font-size: 58px; letter-spacing: 7px;
    color: var(--emboss-blue);
  }
  .card--back .brand { left: 198px; top: 48px; }
  .card--back .brand__mark {
    width: 62px; height: 62px;
    background: var(--ink);
    margin-right: 18px;
  }
  .card--back .brand__name {
    font-size: 35px; letter-spacing: 4px;
    color: var(--ink);
  }
  .holder {
    position: absolute;
    left: 0; right: 0; top: 258px;
    text-align: center;
    font-size: 37px;
    letter-spacing: 1px;
    color: var(--ink);
    text-transform: uppercase;
  }
  .holder__first { font-weight: 700; }
  .holder__last { font-weight: 400; }
  .contact-rail {
    position: absolute;
    left: 0; top: 0;
    width: 702px; height: 401px;
  }
  .contact {
    position: absolute;
    top: 352px;
    font-size: 16px;
    letter-spacing: 0.6px;
    color: var(--ink);
    text-align: center;
    white-space: nowrap;
    transform: translateX(-50%);
  }
  .contact--phone { left: 100px; font-size: 19px; top: 350px; }
  .contact--email { left: 351px; }
  .contact--web { left: 586px; font-size: 15px; top: 353px; }
</style>
</head>
<body>
  <section class="card card--front" aria-label="Card front">
    <div class="brand">
      <span class="brand__mark"></span>
      <span class="brand__name">Oak<br>Partners</span>
    </div>
  </section>

  <section class="card card--back" aria-label="Card back">
    <div class="brand">
      <span class="brand__mark"></span>
      <span class="brand__name">Oak<br>Partners</span>
    </div>

    <p class="holder"><span class="holder__first">Dorian</span> <span class="holder__last">Pemberton</span></p>

    <svg class="contact-rail" viewBox="0 0 702 401" aria-hidden="true">
      <g stroke="var(--ink)" stroke-width="2">
        <line x1="25" y1="326" x2="676" y2="326"/>
      </g>
      <g fill="var(--ink)" stroke="#fff" stroke-width="2">
        <circle cx="100" cy="326" r="16"/>
        <circle cx="351" cy="326" r="16"/>
        <circle cx="583" cy="326" r="16"/>
      </g>
      <!-- phone -->
      <path d="M94 318 q-3 3 0 8 q4 7 10 9 q4 1 6 -2 l-3 -3 q-2 1 -4 0 q-3 -2 -5 -5 q-1 -2 1 -3 z" fill="#fff"/>
      <!-- envelope -->
      <g fill="none" stroke="#fff" stroke-width="1.6">
        <rect x="342" y="320" width="18" height="13" rx="1"/>
        <path d="M342 321 l9 7 l9 -7"/>
      </g>
      <!-- globe -->
      <g fill="none" stroke="#fff" stroke-width="1.5">
        <circle cx="583" cy="326" r="8"/>
        <ellipse cx="583" cy="326" rx="3.5" ry="8"/>
        <line x1="575" y1="326" x2="591" y2="326"/>
      </g>
    </svg>

    <span class="contact contact--phone">800-555-0147</span>
    <span class="contact contact--email">dorian@oakpartners.example</span>
    <span class="contact contact--web">www.oakpartners.example</span>
  </section>
</body>
</html>
```